Business card design Needed for new logo / Construction business, home extensions and new builds

We need a business card design using our new logo files which i will attach to this project :)

We are a small construction business specialising in home extensions, new builds and property development. We are very ambitious and would appreciate professional and elegant designs for our new business card.

Very serious about using the services on MakerQuarry and recently acquired our new logo from here :)

Please get involved, i will feedback when i can as i am very busy but can respond daily, thanks

Target Market(s)

People that want to build onto their houses, new building developments or adding too their existing property

Industry/Entity Type

Construction

Contact Information for Business Card

Renwick Tolliver Construction, Lionel Ashby (Managing Director), Tel 07822254961, email - info@renwick-tolliver, www.renwick-tolliver.co.uk

Colors

Designer to choose colors to be used in the design.

Requirements
Must have
• I like a deep grey on the back please. A lot of you have provided black from and back, try mixing things up a little. The black looks cool 😎 Thanks

```html
<!DOCTYPE html>
<html lang="en">
<head>
<meta charset="utf-8">
<title>Renwick Tolliver Construction – Business Card</title>
<link href="https://fonts.googleapis.com/css2?family=Open+Sans:wght@400;600;700&display=swap" rel="stylesheet">
<style>
  :root {
    --stage: #232323;
    --card: #1d1d20;
    --card-back: #18181b;
    --gold: #f0b323;
    --gold-deep: #c98a12;
    --silver: #d9d9d9;
    --text: #f4f4f4;
    --line: rgba(255,255,255,0.75);
  }
  * { box-sizing: border-box; margin: 0; padding: 0; }
  html, body {
    width: 1200px; height: 780px; overflow: hidden;
    background: var(--stage);
    font-family: "Open Sans", sans-serif;
  }
  .canvas { position: relative; width: 1200px; height: 780px; }

  .card {
    position: absolute;
    width: 540px; height: 310px;
    border-radius: 18px;
    overflow: hidden;
    box-shadow: -3px 3px 0 var(--gold), -4px 5px 0 var(--gold-deep), 0 18px 40px rgba(0,0,0,0.55);
  }

  /* Back side */
  .card-back { left: 50px; top: 100px; background: var(--card-back); }
  .pattern-field {
    position: absolute; inset: 0;
    background: linear-gradient(160deg, #4a4a4d 0%, #2a2a2d 30%, #161618 60%, #121214 100%);
  }
  .back-brand {
    position: absolute; right: 26px; bottom: 30px;
    display: flex; align-items: center; gap: 6px;
    color: var(--gold); font-size: 9px; font-weight: 600; letter-spacing: 0.5px;
    text-transform: uppercase;
  }
  .back-brand .brand-square { width: 10px; height: 10px; background: var(--gold); }

  /* Front side */
  .card-front { left: 610px; top: 380px; background: linear-gradient(150deg, #26262a 0%, var(--card) 55%, #1a1a1d 100%); }
  .faint-mark {
    position: absolute; left: 215px; top: 40px; width: 230px; height: 210px;
    background: radial-gradient(ellipse at 50% 55%, rgba(255,255,255,0.05), rgba(255,255,255,0) 70%);
  }
  .identity { position: absolute; left: 60px; top: 138px; }
  .person-name { font-size: 30px; font-weight: 700; line-height: 1; letter-spacing: 0.5px; }
  .first-name {
    background: linear-gradient(90deg, #bdbdbd, #f2f2f2);
    -webkit-background-clip: text; background-clip: text; color: transparent;
  }
  .last-name {
    background: linear-gradient(90deg, #f3c04a, var(--gold-deep));
    -webkit-background-clip: text; background-clip: text; color: transparent;
  }
  .person-role { color: var(--text); font-size: 14px; font-weight: 600; margin: 6px 0 0 112px; }

  .divider { position: absolute; left: 300px; top: 92px; width: 1px; height: 120px; background: var(--line); }

  .contacts { position: absolute; left: 320px; top: 98px; list-style: none; }
  .contacts li {
    display: flex; align-items: center; gap: 8px;
    color: var(--text); font-size: 12.5px; line-height: 1; margin-bottom: 12px;
  }
  .contacts svg { width: 13px; height: 13px; flex: none; }

  .address {
    position: absolute; left: 0; right: 0; bottom: 34px;
    text-align: center; color: var(--text); font-size: 14px; letter-spacing: 0.3px;
  }
</style>
</head>
<body>
<main class="canvas">

  <section class="card card-back" aria-label="Card back">
    <div class="pattern-field" role="img" aria-label="Repeating brand pattern with glossy light sheen across the upper area"></div>
    <div class="back-brand">
      <span class="brand-square"></span>
      <span class="brand-name">Renwick Tolliver Construction</span>
    </div>
  </section>

  <section class="card card-front" aria-label="Card front">
    <div class="faint-mark" role="img" aria-label="Faint brand watermark"></div>

    <div class="identity">
      <h1 class="person-name"><span class="first-name">Lionel</span> <span class="last-name">Ashby</span></h1>
      <p class="person-role">Managing Director</p>
    </div>

    <span class="divider"></span>

    <ul class="contacts">
      <li>
        <svg viewBox="0 0 24 24" aria-hidden="true"><path fill="#f0b323" d="M6.6 10.8a15.1 15.1 0 0 0 6.6 6.6l2.2-2.2a1 1 0 0 1 1-.25 11.4 11.4 0 0 0 3.6.57 1 1 0 0 1 1 1V20a1 1 0 0 1-1 1A17 17 0 0 1 3 4a1 1 0 0 1 1-1h3.5a1 1 0 0 1 1 1c0 1.25.2 2.45.57 3.6a1 1 0 0 1-.25 1z"/></svg>
        <span>0782 225 4961</span>
      </li>
      <li>
        <svg viewBox="0 0 24 24" aria-hidden="true"><circle cx="12" cy="12" r="9" fill="none" stroke="#f0b323" stroke-width="2"/><path d="M3 12h18M12 3c3 3 3 15 0 18M12 3c-3 3-3 15 0 18" fill="none" stroke="#f0b323" stroke-width="1.6"/></svg>
        <span>info@renwick-tolliver.co.uk</span>
      </li>
      <li>
        <svg viewBox="0 0 24 24" aria-hidden="true"><rect x="3" y="6" width="18" height="13" rx="1.5" fill="none" stroke="#f0b323" stroke-width="2"/><path d="M3.5 7l8.5 6.5L20.5 7" fill="none" stroke="#f0b323" stroke-width="2"/></svg>
        <span>www.renwick-tolliver.co.uk</span>
      </li>
    </ul>

    <p class="address">Larkspur Road, Elmhurst Westbay, WB4 2QF</p>
  </section>

</main>
</body>
</html>
```